Modernize and improve usability of our webpage www.lernwandel.ch (4 languages, mostly static content)

Need to modernize and freshen up the webpages of our association: www.lernwandel.ch We offer apprenticeship exchanges within Switzerland and abroad. Young people can inform and enroll online. We do the matchmaking with work locations and organize logistics, stay overs etc.
The webpage needs to be in 4 languages (German, French, Italian and English). The main pages will be:
- Landing page: what we do, targeted to our apprentices / young people who enroll for the stages.
- Sup-Page: Registration form for interested apprentices to sign up for the program
- Sub-Page "Company", the firms who would like to send their apprentices on a internship and info on how to join the program
- Sub-Page "Host Family", private people who would be interested in hosting the apprentices (for free) during the stages. Find out about the reqiurements for the host families
- Sub-Page "About Us", who we are, executive team, board of director, our sponsor "Falkner Circle Switzerland"
- Footer: contact (E-Mail, Telephone, WhatsApp), Bank details (IBAN Number), Partnerlogo of Falkner-Circle (see uploaded jpg), Social-Media Links (Facebook, LinkedIn)

Target Market(s)

Young people looking for a "apprenticeship" stage within Switzerland or going from Switzerland abroad

Industry/Entity Type

Apprenticeships: cooks, builders, craftsman, office support, etc.

Number of Pages Required

5+ page

Font styles to use
Other font styles liked:
• Lato (sans serif)

Requirements
Must have
• use colors shown on uploaded PDF-Slides: Make the BLUE the MAIN color, the ORANGE as a secondary color
Nice to have
• Forms using e.g. google forms or survey-monkey forms (external links, no code). Matching & appealing visuals showing young apprentices (can use stock photos)

```html
<!DOCTYPE html>
<html lang="en">
<head>
<meta charset="utf-8">
<title>Lernwandel – Apprenticeship Exchanges</title>
<link href="https://fonts.googleapis.com/css2?family=Lato:wght@300;400;700;900&display=swap" rel="stylesheet">
<style>
:root{
  --blue:#3b95f7;
  --blue-dark:#2a5897;
  --navy:#2c4a7c;
  --orange:#ff6200;
  --orange-soft:#ff7a2a;
  --white:#ffffff;
  --text:#4a5a75;
  --muted:#eef4fd;
}
*{margin:0;padding:0;box-sizing:border-box}
html,body{width:1200px;height:3927px;overflow:hidden}
body{position:relative;font-family:'Lato',sans-serif;color:var(--navy);background:var(--white)}
h1,h2,h3,h4{font-weight:400}
.abs{position:absolute}
.btn{position:absolute;display:flex;align-items:center;justify-content:center;font-size:11px;font-weight:700;border-radius:2px;box-shadow:0 4px 10px rgba(0,0,0,.15)}
.btn-blue{background:var(--blue);color:var(--white)}
.btn-orange{background:var(--orange);color:var(--white)}
.btn-white{background:var(--white);color:var(--blue)}
.wave{position:absolute;left:0;width:1200px}

/* header */
.site-header{position:absolute;top:0;left:0;width:1200px;height:75px;background:var(--white);z-index:5}
.brand{position:absolute;left:125px;top:16px;font-size:36px;font-weight:900;color:var(--blue);letter-spacing:-.5px}
.nav a{position:absolute;top:30px;font-size:11px;color:var(--navy);text-decoration:none}
.nav a.active{color:var(--orange)}
.login{position:absolute;left:824px;top:30px;font-size:11px;color:var(--orange);font-weight:700}
.lang{position:absolute;left:993px;top:18px;width:82px;height:38px;background:#8fa6c6;border-radius:2px;color:var(--white);font-size:11px;display:flex;align-items:center;padding-left:10px;gap:6px}
.flag{width:20px;height:12px;background:linear-gradient(#c33 0 50%,#fff 50%);border:1px solid #fff}

/* hero */
.hero-bg{position:absolute;left:0;top:75px;width:1200px;height:460px;background:linear-gradient(135deg,#1f4d8c,#2f6fc0 55%,#3c86d6)}
.hero-title{position:absolute;left:0;top:208px;width:1200px;text-align:center;color:var(--white);font-size:38px;font-weight:300;line-height:46px}
.hero-title b{font-weight:700}

/* what we do */
.eyebrow{position:absolute;font-size:13px;font-weight:700}
.intro-title{position:absolute;left:125px;top:748px;width:360px;font-size:22px;font-weight:400;line-height:28px;color:var(--navy)}
.trade{position:absolute;width:181px;height:200px;border-radius:4px;overflow:hidden;box-shadow:0 6px 16px rgba(0,0,0,.12)}
.trade .ph{position:absolute;inset:0}
.trade span{position:absolute;left:0;right:0;bottom:28px;text-align:center;color:var(--white);font-size:14px;font-weight:700;z-index:2}
.trade::after{content:"";position:absolute;left:0;right:0;bottom:0;height:90px;background:linear-gradient(transparent,rgba(59,149,247,.85))}

/* companies */
.section-title{position:absolute;left:0;width:1200px;text-align:center;font-weight:400}
.company{position:absolute;top:1343px;width:300px}
.company .ph{height:187px;border-radius:3px}
.company .name-tab{position:absolute;left:25px;top:163px;width:250px;height:30px;background:var(--blue)}
.company h3{position:absolute;top:182px;width:300px;text-align:center;color:var(--white);font-size:15px;font-weight:700}
.company p{position:absolute;top:210px;left:20px;width:260px;text-align:center;color:var(--white);font-size:10px;line-height:19px}

/* host family */
.host-text h2{position:absolute;left:200px;top:1900px;width:340px;font-size:23px;font-weight:400;line-height:30px;color:var(--white)}
.host-text p{position:absolute;left:200px;top:2013px;width:355px;font-size:10px;line-height:19px;color:var(--white)}

/* about */
.about-title{position:absolute;left:240px;top:2414px;width:720px;text-align:center;font-size:23px;font-weight:400;line-height:30px;color:var(--navy)}
.about-body{position:absolute;left:245px;top:2526px;width:710px;text-align:center;font-size:10px;line-height:19px;color:var(--navy)}
.member{position:absolute;width:250px;height:162px;background:var(--orange);border-radius:3px;box-shadow:0 6px 16px rgba(0,0,0,.12)}
.member .avatar{position:absolute;left:25px;top:-58px;width:138px;height:138px;border-radius:50%;background:linear-gradient(160deg,#d7d9dc,#9aa0a8)}
.member h4{position:absolute;left:25px;top:100px;color:var(--white);font-size:15px;font-weight:700}
.member small{position:absolute;left:25px;top:121px;color:var(--white);font-size:10px}
.member .dots{position:absolute;right:8px;top:96px;width:52px;height:62px;background-image:radial-gradient(rgba(255,255,255,.45) 1.2px,transparent 1.5px);background-size:13px 13px}

/* apply */
.apply-title{position:absolute;left:125px;top:3212px;width:470px;font-size:30px;line-height:36px;color:var(--white);font-weight:300}
.apply-title b{font-weight:900}
.survey{position:absolute;left:644px;top:3032px;width:430px;height:430px;border-radius:50%;background:linear-gradient(180deg,var(--orange-soft) 0%,#e8773a 35%,#6d86c7 80%,var(--blue) 100%)}
.survey-head{position:absolute;left:680px;top:3073px;width:355px;text-align:center;color:var(--white);font-size:22px;font-weight:300;line-height:28px}
.survey-head b{font-weight:700;border-bottom:1px solid rgba(255,255,255,.8);padding:0 90px}
.q{position:absolute;left:742px;top:3153px;font-size:12px;font-weight:700;color:var(--white)}
.opt{position:absolute;left:742px;font-size:11px;color:var(--white);display:flex;align-items:center;gap:11px}
.opt i{width:11px;height:11px;border:1px solid var(--white);border-radius:50%;display:inline-block;position:relative}
.opt i.on::after{content:"";position:absolute;inset:2px;border-radius:50%;background:var(--white)}

/* footer */
.footer{position:absolute;left:0;top:3490px;width:1200px;height:437px;background:var(--blue-dark)}
.foot-brand{position:absolute;left:125px;top:3610px;font-size:44px;font-weight:900;color:var(--white);line-height:50px;letter-spacing:-.5px}
.foot-tag{position:absolute;left:125px;top:3688px;width:230px;font-size:10px;line-height:15px;color:var(--white)}
.foot-h{position:absolute;top:3598px;font-size:14px;font-weight:700;color:var(--white)}
.contact-item{position:absolute;left:406px;font-size:12px;color:var(--white);display:flex;gap:10px;line-height:16px}
.contact-item svg{flex:none;margin-top:1px}
.qlink{position:absolute;left:650px;font-size:10px;color:var(--white)}
.news-input{position:absolute;left:818px;top:3633px;width:276px;height:36px;background:var(--white);border-radius:2px;font-size:10px;color:var(--navy);padding:12px 18px}
.small{position:absolute;font-size:10px;color:var(--white)}
.social{position:absolute;top:3804px;width:29px;height:29px;border-radius:50%}
.partner{position:absolute;left:818px;top:3798px;display:flex;align-items:center;gap:10px;color:var(--white);font-size:24px;font-weight:700}
.partner .mark{width:36px;height:36px;border-radius:50%;background:#e6b325}
</style>
</head>
<body>

<header class="site-header">
  <div class="brand">lernwandel</div>
  <nav class="nav">
    <a class="active" style="left:424px">Home</a>
    <a style="left:480px">Company</a>
    <a style="left:553px">Host Family</a>
    <a style="left:638px">About Us</a>
    <a style="left:710px">Contact Us</a>
  </nav>
  <div class="login">
    <svg width="10" height="10" viewBox="0 0 10 10" style="vertical-align:-1px"><circle cx="5" cy="3" r="2.4" fill="#ff6200"/><path d="M0.5 10a4.5 4 0 0 1 9 0z" fill="#ff6200"/></svg>
    Login
  </div>
  <div class="btn btn-blue" style="left:880px;top:18px;width:101px;height:38px">Apply Now!</div>
  <div class="lang"><span class="flag"></span>En<svg width="8" height="5" style="margin-left:16px"><path d="M0 0l4 4 4-4" fill="none" stroke="#fff"/></svg></div>
</header>

<section class="hero">
  <div class="hero-bg" role="img" aria-label="Apprentice cook working in a professional kitchen, tinted blue"></div>
  <h1 class="hero-title">We offer <b>apprenticeship</b> exchanges within<br><b>Switzerland and abroad</b></h1>
  <div class="btn btn-orange" style="left:536px;top:325px;width:126px;height:37px">Contact Us Today</div>
  <svg class="wave" style="top:455px" height="90" viewBox="0 0 1200 90"><path d="M0 50C180 90 390 85 600 50S930 -5 1040 10 1160 30 1200 38V90H0Z" fill="#fff"/></svg>
</section>

<section class="what-we-do">
  <div class="eyebrow" style="left:125px;top:720px;color:#e0381c">What We Do</div>
  <h2 class="intro-title">Falkner Circle Switzerland/Liechtenstein mainly supports this program with the objective of promoting the mobility of apprentices</h2>
  <div class="btn btn-blue" style="left:125px;top:903px;width:113px;height:37px">Apply now!</div>

  <div class="trade" style="left:481px;top:732px"><div class="ph" role="img" aria-label="Cook chopping vegetables" style="background:linear-gradient(160deg,#d7b36a,#8ea0a8 60%,#5a8ccc)"></div><span>Cooks</span></div>
  <div class="trade" style="left:687px;top:619px"><div class="ph" role="img" aria-label="Young builder in hard hat and safety vest" style="background:linear-gradient(160deg,#c9bfae,#d48a4e 55%,#7e8ea0)"></div><span>Builders</span></div>
  <div class="trade" style="left:893px;top:732px"><div class="ph" role="img" aria-label="Office support apprentice with headset" style="background:linear-gradient(160deg,#b06a4e,#d9c8bf 50%,#8fa7c8)"></div><span>Office Support</span></div>
  <div class="trade" style="left:687px;top:844px"><div class="ph" role="img" aria-label="Craftsman working with wood shavings" style="background:linear-gradient(160deg,#8a95a0,#c8c1b4 55%,#7a96bd)"></div><span>Craftsman</span></div>
</section>

<section class="companies">
  <svg class="wave" style="top:1110px" height="680" viewBox="0 0 1200 680"><path d="M0 80C200 60 420 20 560 10S780 -5 880 20 1100 60 1200 60V680H0Z" fill="#3b95f7"/></svg>
  <div class="section-title" style="top:1225px;font-size:13px;color:var(--white)">Companies</div>
  <h2 class="section-title" style="top:1262px;font-size:22px;line-height:27px;color:var(--white)">Every successful company builds on well educated and<br>motivated professionals.</h2>

  <article class="company" style="left:125px">
    <div class="ph" role="img" aria-label="Modern office building at night with red lights" style="background:linear-gradient(160deg,#c23a2a,#e4823a 45%,#4a4b55)"></div>
    <div class="name-tab"></div>
    <h3>Brunnholz Architektur AG</h3>
    <p>Our office Brunnholz Architektur AG, with headquarters near Zurich, is primarily active in the planning and...</p>
  </article>
  <article class="company" style="left:450px">
    <div class="ph" role="img" aria-label="Welder working in an industrial workshop with sparks" style="background:linear-gradient(160deg,#6c7680,#f0a02a 50%,#5c6168)"></div>
    <div class="name-tab"></div>
    <h3>Kessler Anlagenbau AG</h3>
    <p>Die Firma Kessler AG is a well-known maker of process systems and glass equipment such as reactors, filter ...</p>
  </article>
  <article class="company" style="left:775px">
    <div class="ph" role="img" aria-label="Tailor measuring green fabric" style="background:linear-gradient(160deg,#c8c59a,#2aa38a 55%,#e7e0c8)"></div>
    <div class="name-tab"></div>
    <h3>Textura</h3>
    <p>Textura, the Swiss technical school for fashion and design, has a leading position in the Swiss fashion landscape.</p>
  </article>
  <div class="btn btn-orange" style="left:525px;top:1657px;width:150px;height:36px">View All Companies</div>
</section>

<section class="host-family">
  <svg class="wave" style="top:1710px" height="600" viewBox="0 0 1200 600"><path d="M0 60C250 80 500 60 700 40S1050 -5 1200 10V500C1100 520 950 570 760 585S300 520 150 525 0 540 0 540Z" fill="#ff6200"/></svg>
  <div class="eyebrow" style="left:200px;top:1866px;color:var(--white)">Host Family</div>
  <div class="host-text">
    <h2>Lorem Ipsum is simply dummy text of the printing and typesetting industry.</h2>
    <p>It is a long established fact that a reader will be distracted by the readable content of a page when looking at its layout. The point of using Lorem Ipsum is that it has a more-or-less normal distribution of letters, as opposed to using 'Content here, content here...</p>
  </div>
  <div class="btn btn-blue" style="left:200px;top:2113px;width:150px;height:37px">About The Host Families</div>
  <div class="abs" role="img" aria-label="Chef teaching young apprentices to cook" style="left:612px;top:1820px;width:388px;height:388px;border-radius:50% 50% 50% 0;background:linear-gradient(150deg,#b9884c,#e9e3da 45%,#c23a2a 80%,#5e8a3c)"></div>
</section>

<section class="about">
  <div class="eyebrow" style="left:0;width:1200px;text-align:center;top:2376px;color:var(--blue)">About Us</div>
  <h2 class="about-title">Lernwandel has been organizing the exchange of apprentices between different cultural and language regions within Switzerland as well as with other countries for more than 19 years.</h2>
  <p class="about-body">Primary participants are all apprentices who are completing their basic vocational education and training.<br>Once registered for the exchange, Lernwandel will find a suitable exchange company and an appropriate accommodation, where the apprentice will go through an exchange of at least three weeks. Falkner Circle Switzerland/Liechtenstein mainly supports this program with the objective of promoting the mobility of apprentices.</p>
  <div class="btn btn-blue" style="left:524px;top:2623px;width:150px;height:37px">Discover More About</div>

  <div class="member" style="left:200px;top:2697px"><div class="avatar" role="img" aria-label="Portrait photo of team member"></div><h4>Lena Amsler</h4><small>Co-Managing Director</small><div class="dots"></div></div>
  <div class="member" style="left:475px;top:2772px"><div class="avatar" role="img" aria-label="Portrait photo of team member"></div><h4>Sara Hofstetter</h4><small>Co-Managing Director</small><div class="dots"></div></div>
  <div class="member" style="left:750px;top:2697px"><div class="avatar" role="img" aria-label="Portrait photo of team member"></div><h4>Giulia Marchetti</h4><small>Contact for Romandie</small><div class="dots"></div></div>
  <div class="btn btn-blue" style="left:544px;top:2967px;width:112px;height:37px">View All Team</div>
</section>

<section class="apply">
  <svg class="wave" style="top:3078px" height="440" viewBox="0 0 1200 440"><path d="M0 0H1200V420C1100 400 1000 370 850 400S500 440 350 420 100 400 0 420Z" fill="#3b95f7"/></svg>
  <div class="survey"></div>
  <div class="survey-head">Employee engagement<br><b>Survey</b></div>
  <div class="q">I am inspired to meet my goals at work.</div>
  <div class="opt" style="top:3191px"><i></i>Strongly agree</div>
  <div class="opt" style="top:3213px"><i class="on"></i>Agree</div>
  <div class="opt" style="top:3236px"><i></i>Neither agree not disagree</div>
  <div class="opt" style="top:3258px"><i></i>Disagree</div>
  <div class="opt" style="top:3281px"><i></i>Strongly disagree</div>
  <div class="btn btn-orange" style="left:742px;top:3331px;width:112px;height:35px">Next</div>
  <div class="abs" role="img" aria-label="Smiling young professional in shirt and tie pointing at the survey" style="left:952px;top:3135px;width:236px;height:355px;border-radius:110px 110px 0 0;background:linear-gradient(180deg,#c9a58a 0%,#f2f2f2 45%,#e8ecf2 100%)"></div>

  <div class="eyebrow" style="left:125px;top:3172px;color:var(--white)">Apply now!</div>
  <h2 class="apply-title"><b>Lernwandel organizes the exchange of apprentices</b> from different language and cultural areas in <b>Switzerland and abroad.</b></h2>
  <div class="btn btn-white" style="left:125px;top:3378px;width:112px;height:37px">Apply now!</div>
</section>

<footer>
  <div class="footer"></div>
  <div class="foot-brand">lernwandel</div>
  <p class="foot-tag">Lernwandel organizes the exchange of apprentices from different language and cultural areas in Switzerland and abroad.</p>

  <div class="foot-h" style="left:406px">Contact Us</div>
  <div class="contact-item" style="top:3635px"><svg width="12" height="12" viewBox="0 0 12 12"><path d="M2 1l2 0 1 3-1.5 1a7 7 0 0 0 3.5 3.5L8 7l3 1v2a1 1 0 0 1-1 1A9 9 0 0 1 1 2a1 1 0 0 1 1-1z" fill="#ff6200"/></svg>+41 (0) 31 555 20 40</div>
  <div class="contact-item" style="top:3665px"><svg width="12" height="12" viewBox="0 0 12 12"><circle cx="6" cy="6" r="5" fill="none" stroke="#ff6200" stroke-width="1.3"/><path d="M4 4l1 0 .6 1.4-.6.6a3 3 0 0 0 1.4 1.4l.6-.6 1.4.6v1" fill="none" stroke="#ff6200"/></svg>+41 79 555 18 62</div>
  <div class="contact-item" style="top:3695px;font-size:11px"><svg width="12" height="10" viewBox="0 0 12 10"><rect x="0.5" y="0.5" width="11" height="9" fill="#ff6200"/><path d="M.5 .5l5.5 5 5.5-5" fill="none" stroke="#2a5897"/></svg>info@lernwandel.ch</div>
  <div class="contact-item" style="top:3727px;font-size:11px"><svg width="12" height="14" viewBox="0 0 12 14"><path d="M6 0a5 5 0 0 1 5 5c0 4-5 9-5 9S1 9 1 5a5 5 0 0 1 5-5z" fill="#ff6200"/><circle cx="6" cy="5" r="2" fill="#2a5897"/></svg><span>Lernwandel<br>Lindenweg 4, 8600 Seewil</span></div>

  <div class="foot-h" style="left:650px">Quick Links</div>
  <div class="qlink" style="top:3632px">Home</div>
  <div class="qlink" style="top:3655px">Company</div>
  <div class="qlink" style="top:3677px">Host Family</div>
  <div class="qlink" style="top:3700px">About Us</div>
  <div class="qlink" style="top:3722px">Contact Us</div>

  <div class="foot-h" style="left:818px">Subscribe Newsletter</div>
  <div class="news-input">name@email.com</div>
  <div class="btn btn-blue" style="left:818px;top:3690px;width:88px;height:36px;box-shadow:none">Submit</div>

  <div class="small" style="left:125px;top:3813px">© 2023 <span style="color:var(--blue)">Lernwandel</span>. All Rights Reserved.</div>
  <div class="small" style="left:405px;top:3813px">Imprint &nbsp;&nbsp; I &nbsp;&nbsp; Privacy policy</div>
  <div class="social" style="left:650px;background:var(--blue)" role="img" aria-label="Social network link"></div>
  <div class="social" style="left:688px;background:var(--orange)" role="img" aria-label="Professional network link"></div>
  <div class="partner"><span>Falkner Circle</span><span class="mark"></span></div>
  <svg class="abs" style="left:1128px;top:3806px" width="20" height="22" viewBox="0 0 20 22"><path d="M10 0L20 22 10 16 0 22Z" fill="#3b95f7"/></svg>
</footer>

</body>
</html>
```